Business Card for Fashion House

We need a business card design for our personalize fashion service for our customers. the business card should reflect reliability, luxury and creativity.
The brand Gravetto is extracted from "Graceful Velvetto"; Gravetto provides fashion designs sprinkled with luxury and style tailored for our elite clients character profile.
Gravetto is created for those who embody class and elegance with a passion for style.
Target Market(s)
Affluent Customers
Industry/Entity Type
Fashion
Contact Information for Business Card
Samira Haddadin
Fashion Designer
Telephone: +971 4 555 0192
Mobile +971 50 555 0147
Emal info@gravetto-example.com
Website www.gravetto-example.com
Social Media Youtube g+ Facebook Instagram Pin /gravetto
Font styles to use
Other font styles liked:
- Audrey provided
Look and feel
Each slider illustrates characteristics of the customer's brand and the style your logo design should communicate.

```html
<!DOCTYPE html>
<html lang="en">
<head>
<meta charset="utf-8">
<title>Gravetto — Business Card</title>
<link rel="stylesheet" href="https://fonts.googleapis.com/css2?family=Marcellus&family=Roboto:wght@400&family=Cormorant+Garamond:wght@500&display=swap">
<style>
  :root {
    --stage: #d8d3ce;
    --frost-light: #f1efed;
    --frost-mid: #dedad6;
    --panel: #1f1e1d;
    --panel-edge: #3a3836;
    --gold: #d2bea3;
    --gold-soft: #c9b89f;
    --ivory: #e8e4de;
    --ink: #2a2a2a;
  }
  html, body {
    margin: 0;
    width: 1200px;
    height: 1054px;
    overflow: hidden;
    background: var(--stage);
  }
  .card {
    position: absolute;
    left: 100px;
    top: 224px;
    width: 1000px;
    height: 606px;
    overflow: hidden;
    box-shadow: 0 18px 40px rgba(0,0,0,.18);
    font-family: "Roboto", Arial, sans-serif;
  }
  .card-shapes {
    position: absolute;
    inset: 0;
  }
  .brand {
    position: absolute;
    left: 61px;
    top: 170px;
    width: 400px;
    text-align: center;
  }
  .brand-circle {
    display: block;
    width: 110px;
    height: 110px;
    margin: 0 auto 38px;
    border: 6px solid var(--ink);
    border-radius: 50%;
    box-sizing: border-box;
  }
  .brand-name {
    font-family: "Cormorant Garamond", Georgia, serif;
    font-weight: 500;
    font-size: 40px;
    letter-spacing: 0.42em;
    margin-right: -0.42em;
    color: var(--ink);
    line-height: 1;
  }
  .holder {
    position: absolute;
    right: 57px;
    top: 62px;
    text-align: right;
  }
  .holder-name {
    font-family: "Marcellus", Georgia, serif;
    font-size: 37px;
    color: var(--gold);
    line-height: 1.1;
  }
  .holder-title {
    font-size: 20px;
    color: var(--ivory);
    margin-top: 6px;
  }
  .contacts {
    position: absolute;
    right: 57px;
    top: 362px;
    margin: 0;
    padding: 0;
    list-style: none;
  }
  .contact-row {
    display: flex;
    justify-content: flex-end;
    align-items: center;
    height: 34.5px;
    font-size: 24px;
    color: var(--gold-soft);
  }
  .contact-icon {
    width: 24px;
    height: 24px;
    margin-left: 20px;
    flex: none;
  }
  .social-row {
    margin-top: 8px;
  }
  .social-dot {
    width: 11px;
    height: 11px;
    border-radius: 50%;
    background: var(--gold-soft);
    margin-left: 13px;
  }
  .social-handle {
    margin-left: 14px;
    color: var(--ivory);
    font-size: 26px;
  }
</style>
</head>
<body>
  <div class="card">
    <svg class="card-shapes" viewBox="0 0 1000 606" width="1000" height="606" aria-hidden="true">
      <defs>
        <linearGradient id="frost" x1="0" y1="0" x2="1" y2="1">
          <stop offset="0" stop-color="var(--frost-light)"/>
          <stop offset="1" stop-color="var(--frost-mid)"/>
        </linearGradient>
      </defs>
      <rect class="frost-side" width="1000" height="606" fill="url(#frost)"/>
      <path class="panel-sheen" d="M452 0 H1000 V606 H446 Q585 303 452 0 Z" fill="var(--panel-edge)" opacity="0.35"/>
      <path class="dark-panel" d="M471 0 H1000 V606 H465 Q602 303 471 0 Z" fill="var(--panel)"/>
    </svg>

    <div class="brand">
      <span class="brand-circle"></span>
      <div class="brand-name">GRAVETTO</div>
    </div>

    <div class="holder">
      <div class="holder-name">Samira Haddadin</div>
      <div class="holder-title">Fashion Designer</div>
    </div>

    <ul class="contacts">
      <li class="contact-row">+971 4 555 0192
        <svg class="contact-icon" viewBox="0 0 24 24" fill="none" stroke="var(--ivory)" stroke-width="1.8" stroke-linejoin="round"><path d="M6 3 L9 3 L10.5 7.5 L8.5 9 Q10 13 15 15.5 L16.5 13.5 L21 15 L21 18 Q21 21 18 21 Q4 19 3 6 Q3 3 6 3 Z"/></svg>
      </li>
      <li class="contact-row">+971 50 555 0147
        <svg class="contact-icon" viewBox="0 0 24 24" fill="none" stroke="var(--ivory)" stroke-width="1.8"><rect x="6" y="2" width="12" height="20" rx="2"/><line x1="10" y1="18.5" x2="14" y2="18.5"/></svg>
      </li>
      <li class="contact-row">info@gravetto-example.com
        <svg class="contact-icon" viewBox="0 0 24 24" fill="none" stroke="var(--ivory)" stroke-width="1.8" stroke-linejoin="round"><rect x="2.5" y="5" width="19" height="14" rx="1"/><path d="M2.5 5.5 L12 13 L21.5 5.5"/></svg>
      </li>
      <li class="contact-row">www.gravetto-example.com
        <svg class="contact-icon" viewBox="0 0 24 24" fill="none" stroke="var(--ivory)" stroke-width="1.6"><circle cx="12" cy="12" r="9.5"/><ellipse cx="12" cy="12" rx="4.2" ry="9.5"/><line x1="2.5" y1="12" x2="21.5" y2="12"/><path d="M4 7 H20 M4 17 H20"/></svg>
      </li>
      <li class="contact-row social-row">
        <span class="social-dot"></span>
        <span class="social-dot"></span>
        <span class="social-dot"></span>
        <span class="social-dot"></span>
        <span class="social-dot"></span>
        <span class="social-handle">/gravetto</span>
      </li>
    </ul>
  </div>
</body>
</html>
```